SnackOrbit!!! A Vending Machine Business Looking for an attractive website.

We are a vending machine business in Northern Michigan. We have changed our name and have rebranded our company. We would like an attractive website that shares who we are, what services we provide, the products we offer in our machines, along with a form businesses can fill out to see if they are a good fit for our company. I would like to have a Home Page, About SnackOrbit, Why Choose SnackOrbit?, Products & Services, Contact Us (With a Login Option), and a page with a questionnaire for thos interested in getting a FREE Vending Machine.

Target Market(s)

Businesses, Campgrounds, Schools, and many more in Northern Michigan

Industry/Entity Type

Vending Machines

Coding

Coded - Design and coding required

Number of Pages Required

5+ page

Requirements
Must have
• An inviting and enticing Home Page. I want to get my potential clients engaged in our website.
Nice to have
• Possibly background photos from Northern Michigan
Should not have
• A corporate feel. I do not want a boring website.

```html
<!DOCTYPE html>
<html lang="en">
<head>
<meta charset="utf-8">
<title>SnackOrbit – Crave. Vend. Repeat.</title>
<link href="https://fonts.googleapis.com/css2?family=Poppins:wght@400;500;600;700&display=swap" rel="stylesheet">
<style>
:root{
  --navy:#1b1f5e;
  --green:#2f5a2a;
  --ink:#3a3a3a;
  --muted:#555;
  --pale:#eef5f5;
  --white:#ffffff;
  --footer:#111214;
}
*{box-sizing:border-box;margin:0;padding:0}
html,body{width:1200px;height:3610px;overflow:hidden}
body{font-family:"Poppins",sans-serif;color:var(--ink);background:var(--white);position:relative}
.abs{position:absolute}
.btn{position:absolute;display:flex;align-items:center;justify-content:center;font-size:16px;border-radius:4px;text-decoration:none}
.btn-green{background:var(--green);color:var(--white);box-shadow:0 2px 4px rgba(0,0,0,.25)}
.btn-white{background:var(--white);color:var(--green)}
.wordmark{font-weight:700;color:var(--navy);font-size:30px;letter-spacing:-.5px;display:flex;align-items:center;gap:8px}
.wordmark .dot{width:14px;height:14px;border-radius:50%;background:var(--green)}
h2.section-title{position:absolute;font-weight:700;color:var(--navy);font-size:40px;line-height:1.2}

/* header */
.site-header{position:absolute;top:0;left:0;width:1200px;height:86px;background:var(--white)}
.site-header .wordmark{position:absolute;left:112px;top:22px}
.main-nav{position:absolute;left:363px;top:30px;display:flex;gap:21px;font-size:16px;color:#222}
.login{left:948px;top:22px;width:141px;height:41px;font-size:17px}

/* hero */
.hero{position:absolute;top:86px;left:0;width:1200px;height:556px;
  background:
    radial-gradient(ellipse 420px 300px at 15% 20%,rgba(150,150,150,.55),transparent 70%),
    radial-gradient(ellipse 380px 260px at 85% 30%,rgba(130,130,130,.45),transparent 70%),
    radial-gradient(ellipse 500px 220px at 50% 85%,rgba(120,120,120,.5),transparent 70%),
    linear-gradient(160deg,#3c3c3c 0%,#262626 50%,#1a1a1a 100%)}
.hero h1{position:absolute;top:180px;left:0;width:1200px;text-align:center;color:var(--white);font-weight:700;font-size:42px;line-height:65px;text-shadow:0 2px 6px rgba(0,0,0,.4)}
.hero .b1{left:415px;top:339px;width:164px;height:40px}
.hero .b2{left:621px;top:339px;width:164px;height:40px}

/* who */
.who-photo{left:112px;top:729px;width:442px;height:488px;
  background:
    radial-gradient(ellipse 150px 240px at 28% 50%,#8f2f2a 0%,#7a2521 55%,rgba(122,37,33,0) 100%),
    radial-gradient(ellipse 110px 190px at 76% 47%,#3a48a8 0%,#2f3a8a 55%,rgba(47,58,138,0) 100%),
    var(--white)}
.who .section-title{left:607px;top:818px}
.who p{position:absolute;left:607px;top:888px;width:506px;font-size:15px;line-height:25.7px;text-align:justify;color:var(--muted)}
.who .btn{left:607px;top:1080px;width:132px;height:41px}

/* why */
.why{position:absolute;top:1293px;left:0;width:1200px;height:583px;background:var(--pale)}
.why .section-title{left:112px;top:116px}
.feature{position:absolute;width:380px;height:110px}
.feature .pic{position:absolute;left:0;top:0;width:101px;height:101px;border-radius:50%}
.pic-1{background:radial-gradient(circle at 65% 45%,#b8a08a,#3c4a78 70%)}
.pic-2{background:radial-gradient(circle at 60% 45%,#6a6e78,#23262c 75%)}
.pic-3{background:radial-gradient(circle at 45% 40%,#d9a24a,#3a5a9a 70%)}
.pic-4{background:radial-gradient(circle at 50% 45%,#5a7aa0,#1e2a40 75%)}
.feature .num{position:absolute;left:0;top:0;width:33px;height:33px;border-radius:50%;background:var(--green);color:var(--white);font-size:16px;display:flex;align-items:center;justify-content:center}
.feature h3{position:absolute;left:118px;top:10px;font-size:19px;font-weight:600;color:#111;line-height:24px;width:250px}
.feature p{position:absolute;left:119px;font-size:13px;line-height:20px;color:var(--muted);width:235px}
.machine{left:915px;top:87px;width:174px;height:410px;border-radius:3px;
  background:
    radial-gradient(ellipse 60px 40px at 45% 18%,#f0e6dc,rgba(240,230,220,0) 80%),
    linear-gradient(90deg,rgba(30,30,30,.0) 0%,rgba(30,30,30,.55) 10%,rgba(30,30,30,.55) 70%,rgba(30,30,30,0) 80%) 0 115px/100% 150px no-repeat,
    linear-gradient(180deg,#a65a38,#8a4428 55%,#6e3219)}

/* products */
.products .section-title{left:0;width:1200px;text-align:center;top:1950px}
.tabs{position:absolute;left:112px;top:2031px;display:flex;gap:14.5px}
.tab{width:184px;height:50px;border:1px solid #bfc5c5;display:flex;align-items:center;justify-content:center;font-size:16px;color:var(--green)}
.tab.active{background:var(--green);color:var(--white);border-color:var(--green);font-size:17px}
.product-photo{left:112px;top:2146px;width:355px;height:355px;border-radius:50%;border:5px solid var(--navy);
  background:
    radial-gradient(ellipse 70px 80px at 50% 38%,#c8322a,rgba(200,50,42,0) 100%),
    radial-gradient(ellipse 60px 80px at 78% 35%,#e0b640,rgba(224,182,64,0) 100%),
    radial-gradient(ellipse 70px 60px at 55% 80%,#2f4f9a,rgba(47,79,154,0) 100%),
    radial-gradient(ellipse 60px 70px at 22% 40%,#b9c27a,rgba(185,194,122,0) 100%),
    linear-gradient(180deg,#9a9a9a,#6e6e6e)}
.products p{position:absolute;left:516px;top:2192px;width:573px;font-size:15px;line-height:25.7px;text-align:justify;color:var(--muted);letter-spacing:.15px}
.products .btn{left:516px;top:2406px;width:132px;height:40px}

/* contact */
.contact{position:absolute;top:2587px;left:0;width:1200px;height:722px;background:var(--pale)}
.contact .section-title{left:0;width:1200px;text-align:center;top:74px;line-height:47px}
.contact .intro{position:absolute;left:0;width:1200px;top:205px;text-align:center;font-size:15px;line-height:26px;color:var(--muted)}
.field{position:absolute;border:1px solid #555;border-radius:10px;background:var(--white);font-size:18px;color:#444;padding:11px 18px}
.contact .btn{left:533px;top:603px;width:132px;height:39px}

/* footer */
.site-footer{position:absolute;top:3309px;left:0;width:1200px;height:301px;
  background:
    radial-gradient(ellipse 300px 140px at 50% 30%,rgba(70,60,50,.55),transparent 75%),
    radial-gradient(ellipse 250px 120px at 10% 40%,rgba(60,60,70,.5),transparent 75%),
    radial-gradient(ellipse 250px 120px at 90% 40%,rgba(60,60,70,.5),transparent 75%),
    linear-gradient(180deg,#1c1d20,var(--footer))}
.site-footer .wordmark{position:absolute;left:0;width:1200px;justify-content:center;top:95px;color:var(--white);font-size:44px}
.site-footer .wordmark .dot{background:var(--white)}
.foot-nav{position:absolute;top:190px;left:0;width:1200px;display:flex;justify-content:center;gap:24px;color:var(--white);font-size:17px}
.foot-nav span::before{content:"›";margin-right:6px;font-weight:600}
.foot-rule{position:absolute;left:112px;top:248px;width:977px;height:1px;background:#555}
.copy{position:absolute;top:260px;left:0;width:1200px;text-align:center;color:#bbb;font-size:14px}
</style>
</head>
<body>

<header class="site-header">
  <div class="wordmark"><span class="dot"></span>SnackOrbit</div>
  <nav class="main-nav"><span>Home</span><span>About Us</span><span>Why Choose SnackOrbit?</span><span>Products</span><span>Contact Us</span></nav>
  <a class="btn btn-green login">Login</a>
</header>

<section class="hero" role="img" aria-label="Close-up of vending machine spiral coils and numbered slots in dark tones">
  <h1>SnackOrbit: Crave. Vend. Repeat.<br>Elevating Snacking, One Vend at a Time</h1>
  <a class="btn btn-green b1">Check Services</a>
  <a class="btn btn-white b2">Get A Quote</a>
</section>

<section class="who">
  <div class="abs who-photo" role="img" aria-label="A red and a blue snack vending machine side by side"></div>
  <h2 class="section-title">Who We Are</h2>
  <p>Welcome to SnackOrbit, where snacking meets delight! We’re not just about vending machines; we’re your culinary companions, your flavor curators, and your secret stash of happiness. Daniel and Nora, the dynamic duo behind SnackOrbit, have a passion for all things tasty. With backgrounds in sales and a penchant for personal connections, they’ve transformed the vending experience into an art form.</p>
  <a class="btn btn-green">Learn More</a>
</section>

<section class="why">
  <h2 class="section-title">Why Choose SnackOrbit?</h2>
  <div class="feature" style="left:112px;top:211px">
    <div class="pic pic-1" role="img" aria-label="Customer choosing from a vending machine"></div><div class="num">01</div>
    <h3>Local Love</h3>
    <p style="top:44px">We celebrate the heart of Michigan by partnering with local legends.</p>
  </div>
  <div class="feature" style="left:506px;top:211px">
    <div class="pic pic-2" role="img" aria-label="Hand pressing a vending machine keypad"></div><div class="num">02</div>
    <h3>Unleash Your Cravings</h3>
    <p style="top:44px">SnackOrbit isn’t bound by corporate ties. We’re the rebels of the vending</p>
  </div>
  <div class="feature" style="left:112px;top:354px">
    <div class="pic pic-3" role="img" aria-label="Person enjoying a drink beside a vending machine"></div><div class="num">03</div>
    <h3>Quality Meets Convenience</h3>
    <p style="top:58px;text-align:justify">You’re mid-meeting, and your stomach growls.</p>
  </div>
  <div class="feature" style="left:506px;top:354px">
    <div class="pic pic-4" role="img" aria-label="Fully stocked snack vending machine"></div><div class="num">04</div>
    <h3>Pandemic-Proof &amp; Recession-Ready</h3>
    <p style="top:58px">Life throws curveballs, but SnackOrbit stands strong</p>
  </div>
  <div class="abs machine" role="img" aria-label="Coffee vending machine decorated with coffee beans"></div>
</section>

<section class="products">
  <h2 class="section-title">Our Products</h2>
  <div class="tabs">
    <div class="tab active">Food &amp; Snacks</div>
    <div class="tab">Drinks &amp; Coffee</div>
    <div class="tab">Gumball &amp; Candy</div>
    <div class="tab">Cold &amp; Frozen</div>
    <div class="tab">Custom Machines</div>
  </div>
  <div class="abs product-photo" role="img" aria-label="Candy bars and cookies in vending machine spirals"></div>
  <p>Sed ut perspiciatis unde omnis iste natus error sit voluptatem accusantium doloremque laudantium, totam rem aperiam, eaque ipsa quae ab illo in ventore veritatis et quasi architecto beatae vitae dicta sunt explicabo. Nemo enim ipsam voluptatem quia voluptas sit aspernatur aut odit aut fugit, sed quia consequuntur magni dolores eos qui ratione voluptatem sequi nesciunt. Neque porro quisquam est, qui dolorem ipsum quia dolor sit amet, consectetur, adipisci velit,</p>
  <a class="btn btn-green">Get A Quote</a>
</section>

<section class="contact">
  <h2 class="section-title">Ready To Experience The SnackOrbit<br>Difference?</h2>
  <p class="intro">Sign up now and let’s connect. Taste the future of snacking firsthand! Contact us<br>today and explore how our vending magic can elevate your space.</p>
  <div class="field" style="left:109px;top:277px;width:474px;height:47px">First Name</div>
  <div class="field" style="left:614px;top:277px;width:474px;height:47px">Last Name</div>
  <div class="field" style="left:109px;top:354px;width:474px;height:47px">Email Address</div>
  <div class="field" style="left:614px;top:354px;width:474px;height:47px">Phone Number</div>
  <div class="field" style="left:109px;top:431px;width:979px;height:134px">Message Here....</div>
  <a class="btn btn-green">Submit</a>
</section>

<footer class="site-footer" role="img" aria-label="Dimly lit shelves of snacks behind the footer">
  <div class="wordmark"><span class="dot"></span>SnackOrbit</div>
  <nav class="foot-nav"><span>Home</span><span>About Us</span><span>Why Choose SnackOrbit?</span><span>Products</span><span>Contact Us</span></nav>
  <div class="foot-rule"></div>
  <p class="copy">© 2024 SnackOrbit. All Right Reserved.</p>
</footer>

</body>
</html>
```